Product Designer Business Card

Small product design, engineering and prototyping firm in need of a clean, professional business card design. To support our 3D design and drawing services, we offer 3D printing, molding, and casting of plastics, silicones, resins, etc. Our logo can still be modified/changed if necessary. The red/orange color is preferred, but may be substituted with blue or green, potentially. Either way, the colour of the logo should be match/compliment colors used throughout the design. One thought is to have the logo/contact info on one side, with the other side describing services offered, like with a small icon of 3D printer, molding, casting, and computer with a 3D model on-screen.
Industry/Entity Type
Mechanical Engineering
Contact Information for Business Card
Company: Kelvar Design
Phone: 613-582-9047
Email: mark@kelvardesign.ca

```html
<!DOCTYPE html>
<html lang="en">
<head>
<meta charset="utf-8">
<title>Kelvar Design – Business Card</title>
<link href="https://fonts.googleapis.com/css2?family=Exo+2:wght@400;600;700&display=swap" rel="stylesheet">
<style>
  :root {
    --backdrop: #2b2b2c;
    --card: #1e1f21;
    --card-edge: #26272a;
    --red: #d41a10;
    --white: #f2f2f2;
    --rule: #55565a;
    --pattern-top: #34353a;
    --pattern-mid: #2a2b2f;
    --pattern-bottom: #1e1f21;
  }
  * { box-sizing: border-box; margin: 0; padding: 0; }
  html, body { width: 1200px; height: 1108px; overflow: hidden; }
  body {
    background: var(--backdrop);
    font-family: "Exo 2", sans-serif;
    display: flex;
    align-items: center;
    justify-content: center;
    gap: 60px;
  }
  .card {
    width: 420px;
    height: 700px;
    background: var(--card);
    border-radius: 24px;
    border: 1px solid var(--card-edge);
    position: relative;
    overflow: hidden;
    box-shadow: 0 18px 40px rgba(0,0,0,0.45);
  }

  /* Front */
  .card--front { display: flex; flex-direction: column; align-items: center; }
  .brand {
    margin-top: 150px;
    display: flex;
    align-items: center;
    gap: 16px;
  }
  .brand__dot { width: 30px; height: 30px; border-radius: 50%; background: var(--red); }
  .brand__name { font-weight: 600; font-size: 44px; color: var(--red); letter-spacing: 2px; }
  .person { margin-top: 130px; text-align: center; }
  .person__name { font-weight: 700; font-size: 34px; color: var(--red); letter-spacing: 0.5px; }
  .person__title { font-size: 22px; color: var(--white); margin-top: 2px; }
  .divider { margin-top: 22px; width: 250px; display: flex; align-items: center; gap: 8px; }
  .divider__rule { flex: 1; height: 1px; background: var(--rule); }
  .divider__icon {
    width: 26px; height: 26px; background: var(--red); border-radius: 3px;
    display: flex; align-items: center; justify-content: center;
  }
  .contact { margin-top: 20px; text-align: center; color: var(--white); font-size: 22px; line-height: 34px; }
  .contact__accent { color: var(--red); }

  /* Back */
  .pattern {
    position: absolute;
    left: 0; top: 0;
    width: 100%; height: 560px;
    background:
      radial-gradient(ellipse at 70% 30%, rgba(255,255,255,0.05), transparent 60%),
      linear-gradient(165deg, var(--pattern-top) 0%, var(--pattern-mid) 55%, var(--pattern-bottom) 100%);
  }
  .back-brand {
    position: absolute;
    top: 395px; right: 40px;
    display: flex; align-items: center; gap: 14px;
  }
  .back-brand__dot { width: 28px; height: 28px; border-radius: 50%; background: var(--white); }
  .back-brand__name { font-weight: 600; font-size: 44px; color: var(--white); letter-spacing: 4px; }
  .services {
    position: absolute;
    top: 510px; left: 24px; right: 24px;
    display: flex; justify-content: space-between;
  }
  .service { width: 90px; display: flex; flex-direction: column; align-items: center; gap: 10px; }
  .service__icon { width: 66px; height: 66px; }
  .service__label { font-size: 19px; color: var(--white); white-space: nowrap; }
</style>
</head>
<body>

  <section class="card card--front">
    <div class="brand">
      <span class="brand__dot"></span>
      <span class="brand__name">Kelvar Design</span>
    </div>

    <div class="person">
      <div class="person__name">DANIEL BROOKS</div>
      <div class="person__title">Managing Director</div>
    </div>

    <div class="divider">
      <span class="divider__rule"></span>
      <span class="divider__icon" aria-label="Phone">
        <svg width="16" height="16" viewBox="0 0 24 24"><path fill="#fff" d="M6.6 10.8a15.2 15.2 0 0 0 6.6 6.6l2.2-2.2a1 1 0 0 1 1-.25 11.4 11.4 0 0 0 3.6.57 1 1 0 0 1 1 1V20a1 1 0 0 1-1 1A17 17 0 0 1 3 4a1 1 0 0 1 1-1h3.5a1 1 0 0 1 1 1c0 1.25.2 2.45.57 3.57a1 1 0 0 1-.25 1z"/></svg>
      </span>
      <span class="divider__icon" aria-label="Email">
        <svg width="16" height="16" viewBox="0 0 24 24"><rect x="3" y="6" width="18" height="12" fill="#fff"/><path d="M3 6l9 7 9-7" fill="none" stroke="#d41a10" stroke-width="2"/></svg>
      </span>
      <span class="divider__icon" aria-label="Website">
        <svg width="16" height="16" viewBox="0 0 24 24"><circle cx="12" cy="12" r="9" fill="none" stroke="#fff" stroke-width="2"/><ellipse cx="12" cy="12" rx="4" ry="9" fill="none" stroke="#fff" stroke-width="1.6"/><line x1="3" y1="12" x2="21" y2="12" stroke="#fff" stroke-width="1.6"/></svg>
      </span>
      <span class="divider__rule"></span>
    </div>

    <div class="contact">
      <div>613-582-9047</div>
      <div>mark@kelvardesign.ca</div>
      <div>www.<span class="contact__accent">kelvardesign</span>.ca</div>
    </div>
  </section>

  <section class="card card--back">
    <div class="pattern" role="img" aria-label="Faint repeating brand-name pattern in dark grey"></div>

    <div class="back-brand">
      <span class="back-brand__dot"></span>
      <span class="back-brand__name">Kelvar</span>
    </div>

    <div class="services">
      <div class="service">
        <svg class="service__icon" viewBox="0 0 66 66" role="img" aria-label="3D printer">
          <rect x="8" y="6" width="50" height="50" rx="3" fill="none" stroke="#f2f2f2" stroke-width="5"/>
          <rect x="13" y="12" width="40" height="6" fill="#f2f2f2"/>
          <rect x="28" y="18" width="10" height="10" fill="#f2f2f2"/>
          <path d="M33 28v4" stroke="#f2f2f2" stroke-width="3"/>
          <rect x="20" y="36" width="26" height="10" fill="#f2f2f2"/>
          <rect x="12" y="56" width="8" height="6" fill="#f2f2f2"/>
          <rect x="46" y="56" width="8" height="6" fill="#f2f2f2"/>
        </svg>
        <span class="service__label">3D Printer</span>
      </div>
      <div class="service">
        <svg class="service__icon" viewBox="0 0 66 66" role="img" aria-label="Molding press">
          <rect x="27" y="2" width="12" height="10" fill="#f2f2f2"/>
          <rect x="18" y="12" width="30" height="8" fill="#f2f2f2"/>
          <rect x="30" y="20" width="6" height="8" fill="#f2f2f2"/>
          <path d="M12 30h42v10H40l-4 6h-6l-4-6H12z" fill="#f2f2f2"/>
          <path d="M12 46h14l4 6h6l4-6h14v10H12z" fill="none" stroke="#f2f2f2" stroke-width="4"/>
          <rect x="6" y="58" width="54" height="6" fill="#f2f2f2"/>
        </svg>
        <span class="service__label">Molding</span>
      </div>
      <div class="service">
        <svg class="service__icon" viewBox="0 0 66 66" role="img" aria-label="Casting ladle pouring">
          <path d="M14 4v16" stroke="#f2f2f2" stroke-width="3"/>
          <circle cx="14" cy="22" r="4" fill="none" stroke="#f2f2f2" stroke-width="3"/>
          <path d="M8 28l18 4-4 18H10z" fill="#f2f2f2"/>
          <path d="M26 32c8 2 10 10 9 22" fill="none" stroke="#f2f2f2" stroke-width="5"/>
          <path d="M28 58c4-6 12-6 16 0" fill="none" stroke="#f2f2f2" stroke-width="3"/>
          <rect x="10" y="60" width="48" height="4" fill="#f2f2f2"/>
        </svg>
        <span class="service__label">Casting</span>
      </div>
      <div class="service">
        <svg class="service__icon" viewBox="0 0 66 66" role="img" aria-label="Computer monitor showing a 3D cube">
          <rect x="4" y="8" width="58" height="38" rx="3" fill="none" stroke="#f2f2f2" stroke-width="5"/>
          <path d="M33 16l10 5v11l-10 5-10-5V21z" fill="none" stroke="#f2f2f2" stroke-width="3"/>
          <path d="M23 21l10 5 10-5M33 26v11" fill="none" stroke="#f2f2f2" stroke-width="3"/>
          <rect x="29" y="46" width="8" height="10" fill="#f2f2f2"/>
          <rect x="20" y="56" width="26" height="5" fill="#f2f2f2"/>
        </svg>
        <span class="service__label">3d Model</span>
      </div>
    </div>
  </section>

</body>
</html>
```